Business card for event manager / organizer "waiter service"

Draft of a new valuable business card for my company.
Events, personnel service providers, festivals

```html
<!DOCTYPE html>
<html lang="de">
<head>
<meta charset="utf-8">
<title>Feierwerk Service – Visitenkarte</title>
<link rel="stylesheet" href="https://fonts.googleapis.com/css2?family=Poppins:wght@400;600;700&display=swap">
<style>
  :root{
    --stage:#1c1c1e;
    --card-grey:#5b5f66;
    --band-black:#0d0d0d;
    --ink-white:#ffffff;
    --ink-dark:#141414;
    --brand-orange:#e8741c;
    --photo-grey:#3a3c40;
    --overlay:rgba(255,255,255,.55);
  }
  *{box-sizing:border-box;margin:0;padding:0}
  html,body{width:1200px;height:1015px;overflow:hidden}
  body{background:var(--stage);font-family:"Poppins",sans-serif;position:relative}

  .card{position:absolute;left:300px;width:600px;height:390px;overflow:hidden;box-shadow:0 18px 40px rgba(0,0,0,.6)}
  .card--front{top:97px}
  .card--back{top:527px;background:var(--card-grey)}

  /* front */
  .panel{position:absolute;top:0;height:100%}
  .panel--events{left:0;width:40%;background:linear-gradient(160deg,#fff3c4 0%,#f7b54a 40%,#d9761f 75%,#7a2f12 100%)}
  .panel--staff{left:30%;width:40%;background:linear-gradient(180deg,#e4e4e8 0%,#f2f2f2 35%,#d9474f 60%,#c9c9cb 100%)}
  .panel--festival{left:58%;width:42%;background:linear-gradient(200deg,#d9d6f6 0%,#a7a2d8 30%,#e9cfc0 65%,#c68f68 100%)}
  .tag{position:absolute;background:var(--overlay);color:var(--ink-dark);font-weight:600;font-size:18px;line-height:1.15;padding:8px 14px}
  .tag--events{left:60px;bottom:70px}
  .tag--staff{left:210px;top:175px;text-align:center}
  .tag--festival{right:40px;top:150px}

  /* back */
  .portrait{position:absolute;left:55px;top:75px;width:200px;height:200px;border-radius:50%;background:radial-gradient(circle at 50% 45%,#6e6a68 0%,var(--photo-grey) 70%)}
  .contact{position:absolute;left:290px;top:62px;color:var(--ink-white)}
  .contact__name{font-weight:700;font-size:25px;letter-spacing:.5px;text-transform:uppercase;line-height:1.1}
  .contact__role{font-size:19px;margin-bottom:12px}
  .contact__list{list-style:none}
  .contact__item{display:flex;align-items:center;gap:12px;font-size:16px;line-height:28px}
  .contact__item svg{width:16px;height:16px;flex:none;fill:var(--ink-white)}
  .brand{position:absolute;left:60px;top:290px;display:flex;align-items:center;gap:10px}
  .brand__mark{width:30px;height:30px;background:var(--brand-orange)}
  .brand__name{font-weight:700;font-size:22px;color:var(--brand-orange);text-transform:uppercase}
  .band{position:absolute;left:0;bottom:0;width:100%;height:48px;background:var(--band-black);color:var(--ink-white);font-size:16px;display:flex;align-items:center;justify-content:flex-end;padding-right:40px}
</style>
</head>
<body>

<section class="card card--front" aria-label="Vorderseite">
  <div class="panel panel--events" role="img" aria-label="Foto: Konzertpublikum im warmen Bühnenlicht"></div>
  <div class="panel panel--staff" role="img" aria-label="Foto: Kellner mit Fliege hält einen Tellerstapel"></div>
  <div class="panel panel--festival" role="img" aria-label="Foto: Brautpaar tanzt im Konfettiregen"></div>
  <p class="tag tag--events">Events</p>
  <p class="tag tag--staff">Personnel<br>Service<br>Providers</p>
  <p class="tag tag--festival">Festivals</p>
</section>

<section class="card card--back" aria-label="Rückseite">
  <div class="portrait" role="img" aria-label="Porträtfoto des Inhabers"></div>

  <div class="contact">
    <p class="contact__name">Jonas Brenner</p>
    <p class="contact__role">Inhaber</p>
    <ul class="contact__list">
      <li class="contact__item"><svg viewBox="0 0 24 24"><path d="M6.6 10.8a15 15 0 0 0 6.6 6.6l2.2-2.2c.3-.3.7-.4 1-.2 1.1.4 2.3.6 3.6.6.6 0 1 .4 1 1V20c0 .6-.4 1-1 1A17 17 0 0 1 3 4c0-.6.4-1 1-1h3.5c.6 0 1 .4 1 1 0 1.3.2 2.5.6 3.6.1.3 0 .7-.2 1z"/></svg>02361 555 20 14</li>
      <li class="contact__item"><svg viewBox="0 0 24 24"><path d="M6.6 10.8a15 15 0 0 0 6.6 6.6l2.2-2.2c.3-.3.7-.4 1-.2 1.1.4 2.3.6 3.6.6.6 0 1 .4 1 1V20c0 .6-.4 1-1 1A17 17 0 0 1 3 4c0-.6.4-1 1-1h3.5c.6 0 1 .4 1 1 0 1.3.2 2.5.6 3.6.1.3 0 .7-.2 1z"/></svg>0170 555 48 21</li>
      <li class="contact__item"><svg viewBox="0 0 24 24"><path d="M12 2a10 10 0 1 0 0 20 10 10 0 0 0 0-20zm6.9 6h-3a15 15 0 0 0-1.3-3.9A8 8 0 0 1 18.9 8zM12 4c.8 1.2 1.5 2.5 1.9 4h-3.8c.4-1.5 1.1-2.8 1.9-4zM4.3 14a8 8 0 0 1 0-4h3.4a16 16 0 0 0 0 4zm.8 2h3a15 15 0 0 0 1.3 3.9A8 8 0 0 1 5.1 16zm3-8h-3a8 8 0 0 1 4.3-3.9C8.8 5.3 8.4 6.6 8.1 8zM12 20c-.8-1.2-1.5-2.5-1.9-4h3.8c-.4 1.5-1.1 2.8-1.9 4zm2.3-6H9.7a14 14 0 0 1 0-4h4.6a14 14 0 0 1 0 4zm.3 5.9c.6-1.2 1-2.5 1.3-3.9h3a8 8 0 0 1-4.3 3.9zm1.7-5.9a16 16 0 0 0 0-4h3.4a8 8 0 0 1 0 4z"/></svg>www.feierwerk-service.de</li>
      <li class="contact__item"><svg viewBox="0 0 24 24"><path d="M2 5h20v14H2zm2 2v.4l8 5 8-5V7zm0 2.8V17h16V9.8l-8 5z"/></svg>info@feierwerk-service.de</li>
      <li class="contact__item"><svg viewBox="0 0 24 24"><path d="M12 2a7 7 0 0 0-7 7c0 5.3 7 13 7 13s7-7.7 7-13a7 7 0 0 0-7-7zm0 9.5A2.5 2.5 0 1 1 12 6.5a2.5 2.5 0 0 1 0 5z"/></svg>Lindenweg 12, 45700 Musterstadt</li>
    </ul>
  </div>

  <div class="brand">
    <span class="brand__mark"></span>
    <span class="brand__name">Feierwerk Service</span>
  </div>

  <p class="band">www.feierwerk-service.de/aktuell</p>
</section>

</body>
</html>
```